Kelvor Engineers: Why you should hire us keepsake

New design. Open to plastic cards. We are an engineering firm that designs cell phone towers and commercial buildings. Please check out our website www.kelvorstruct.com for more details. We want people to remember our card and for it to be useful if possible. We want the same look and feel on these cards to be translated to other marketing material we may need such as brochures.

Target Market(s)

Architects, Developers and Telecommunication Carriers

Industry/Entity Type

Engineering

Contact Information for Business Card

Card with our company colors, logo, and innovative design with elements related to our industry.

Font styles to use
Sans Serif

Colors
9bcb3c
abd036
0255a3

Requirements
Must have
• Sleek and hip design
Nice to have
• Bright lime green and navy coloring that pops with an innovative design.
Should not have
• A basic and boring design

```html
<!DOCTYPE html>
<html lang="en">
<head>
<meta charset="utf-8">
<title>Kelvor Engineers — Business Card</title>
<link href="https://fonts.googleapis.com/css2?family=Roboto:ital,wght@0,400;0,700;0,900;1,700&family=Roboto+Condensed:wght@500&display=swap" rel="stylesheet">
<style>
  :root {
    --navy: #022c5c;
    --lime: #00ff00;
    --paper: #f1f1f1;
    --ink: #454545;
    --backdrop: #2b2b2b;
    --white: #ffffff;
  }
  * { box-sizing: border-box; margin: 0; padding: 0; }
  html, body { width: 1200px; height: 960px; overflow: hidden; }
  body { background: var(--backdrop); font-family: "Roboto", Arial, sans-serif; position: relative; }

  .card {
    position: absolute; left: 320px; width: 600px; height: 342px;
    border-radius: 22px; overflow: hidden;
  }

  /* Front */
  .card-front { top: 110px; background: var(--navy); }
  .card-front .wordmark {
    position: absolute; top: 212px; left: 0; width: 100%; text-align: center;
    transform: translateY(-100%);
    font-weight: 900; font-size: 96px; line-height: 1; letter-spacing: -2px;
    color: var(--lime);
  }
  .tagline {
    position: absolute; top: 264px; left: 0; width: 100%;
    display: flex; justify-content: center; align-items: center; gap: 4px;
    color: var(--white); font-weight: 700; font-size: 15.5px; letter-spacing: 0.1px;
  }
  .tagline .rule { width: 28px; height: 2px; background: var(--white); }
  .locations {
    position: absolute; top: 285px; left: 0; width: 100%; text-align: center;
    color: var(--white); font-size: 15.5px; letter-spacing: 0.6px;
  }

  /* Back */
  .card-back { top: 493px; background: var(--paper); }
  .card-back .wordmark {
    position: absolute; left: 52px; top: 110px;
    font-weight: 900; font-size: 58px; line-height: 1; letter-spacing: -1px;
    color: var(--navy);
  }
  .divider { position: absolute; left: 303px; top: 100px; width: 1px; height: 102px; background: #b9b9b9; }
  .contact { position: absolute; left: 332px; top: 103px; }
  .contact .person {
    font-family: "Roboto Condensed", "Arial Narrow", sans-serif; font-weight: 500;
    font-size: 22px; color: var(--lime); margin-bottom: 10px; letter-spacing: 0.2px;
  }
  .contact ul { list-style: none; }
  .contact li { display: flex; align-items: center; gap: 9px; font-size: 14.5px; color: var(--ink); height: 19.5px; }
  .contact svg { width: 13px; height: 13px; fill: var(--lime); flex: none; }
  .wave { position: absolute; left: 0; top: 0; width: 600px; height: 342px; }
  .website {
    position: absolute; left: 30px; top: 312px;
    font-weight: 700; font-style: italic; font-size: 13px; color: var(--navy); letter-spacing: 0.4px;
  }
</style>
</head>
<body>
  <section class="card card-front">
    <div class="wordmark">KELVOR</div>
    <div class="tagline"><span class="rule"></span>MULTI-DISCIPLINE ENGINEERING<span class="rule"></span></div>
    <div class="locations">Ashvale | Corbridge | Halstow | Pine Harbor</div>
  </section>

  <section class="card card-back">
    <div class="wordmark">KELVOR</div>
    <div class="divider"></div>
    <div class="contact">
      <div class="person">DANA WHITLOW REYES</div>
      <ul>
        <li><svg viewBox="0 0 24 24"><path d="M6.6 10.8a15.1 15.1 0 0 0 6.6 6.6l2.2-2.2c.3-.3.7-.4 1-.2 1.1.4 2.3.6 3.6.6.6 0 1 .4 1 1V20c0 .6-.4 1-1 1A17 17 0 0 1 3 4c0-.6.4-1 1-1h3.5c.6 0 1 .4 1 1 0 1.3.2 2.5.6 3.6.1.3 0 .7-.2 1z"/></svg>555.014.7302</li>
        <li><svg viewBox="0 0 24 24"><path d="M7 1h10a2 2 0 0 1 2 2v18a2 2 0 0 1-2 2H7a2 2 0 0 1-2-2V3a2 2 0 0 1 2-2zm0 3v14h10V4zm5 15.5a1 1 0 1 0 0 2 1 1 0 0 0 0-2z"/></svg>555.019.4168</li>
        <li><svg viewBox="0 0 24 24"><path d="M2 5h20v14H2zm2 2v.5l8 5 8-5V7l-8 5z"/></svg>dreyes@kelvorstruct.com</li>
      </ul>
    </div>
    <svg class="wave" viewBox="0 0 600 342" aria-hidden="true">
      <path d="M0 252 C150 292 350 312 600 314 L600 342 L0 342Z" fill="var(--navy)"/>
      <path d="M0 270 C160 302 360 318 600 318 L600 342 L0 342Z" fill="var(--white)"/>
      <path d="M0 274 C160 306 360 322 600 322 L600 342 L0 342Z" fill="var(--lime)"/>
    </svg>
    <div class="website">www.kelvorstruct.com</div>
  </section>
</body>
</html>
```